Looking for a cool & simple business-card-design for digital agency

Hi!

We are a web agency that offers Reputation Management, Vextor & Seo Services and software development. We like cool things, we like innovative styles.

We have uploaded our logo.

Project Deadline Extended Reason: Client does not want any designs with the colorful logo. Please send us submissions ONLY with the blac and white logo. What the client would like to see:1) Back of the card: is a silver logo on a black background2) front of the card with all the data, please use white background and black logo thank you Added Friday, May 8, 2015

Industry/Entity Type

Software

```html
<!DOCTYPE html>
<html lang="en">
<head>
<meta charset="utf-8">
<title>Nordfeld AG – Business Card</title>
<link href="https://fonts.googleapis.com/css2?family=Source+Sans+3:ital,wght@0,400;0,600;0,700;1,700&display=swap" rel="stylesheet">
<style>
  :root {
    --backdrop: #8a8a8a;
    --card-white: #ffffff;
    --card-black: #231f20;
    --ink: #231f20;
    --ink-muted: #8c8c8c;
    --silver: #ffffff;
    --shadow: rgba(0, 0, 0, 0.35);
  }
  * { box-sizing: border-box; margin: 0; padding: 0; }
  html, body {
    width: 1200px;
    height: 907px;
    overflow: hidden;
    background: var(--backdrop);
    font-family: "Source Sans 3", "Myriad Pro", Arial, sans-serif;
  }
  .card {
    position: absolute;
    left: 300px;
    width: 601px;
    height: 343px;
    box-shadow: 0 3px 8px var(--shadow);
  }
  .card--front { top: 91px; background: var(--card-white); color: var(--ink); }
  .card--back  { top: 472px; background: var(--card-black); color: var(--silver); }

  .brand {
    position: absolute;
    left: 0;
    right: 0;
    top: 66px;
    text-align: center;
  }
  .brand__name {
    display: inline-flex;
    align-items: center;
    gap: 12px;
    font-size: 36px;
    font-weight: 700;
    line-height: 1;
    color: var(--ink);
  }
  .brand__square {
    width: 26px;
    height: 26px;
    background: var(--ink);
  }
  .brand__tagline {
    margin-top: 8px;
    font-size: 15px;
    font-weight: 400;
    letter-spacing: 4.5px;
    color: var(--ink);
  }

  .contact {
    position: absolute;
    left: 37px;
    top: 227px;
    list-style: none;
    font-size: 15px;
  }
  .contact li {
    display: flex;
    align-items: center;
    height: 22.5px;
  }
  .contact svg {
    width: 15px;
    height: 15px;
    margin-right: 9px;
    fill: var(--ink);
  }

  .person {
    position: absolute;
    right: 37px;
    top: 223px;
    text-align: right;
  }
  .person__name { font-size: 22px; font-weight: 600; line-height: 1.1; }
  .person__title { font-size: 17px; color: var(--ink-muted); line-height: 1.4; margin-bottom: 3px; }
  .person__address { font-size: 15px; line-height: 1.35; font-style: normal; }

  .back-brand {
    position: absolute;
    left: 0;
    right: 0;
    top: 140px;
    display: flex;
    justify-content: center;
    align-items: center;
    gap: 14px;
    font-size: 44px;
    font-weight: 700;
    color: var(--silver);
  }
  .back-brand__square { width: 32px; height: 32px; background: var(--silver); }
  .back-url {
    position: absolute;
    left: 0;
    right: 0;
    top: 282px;
    text-align: center;
    font-size: 14px;
    font-weight: 700;
    font-style: italic;
    letter-spacing: 3.6px;
    color: var(--silver);
  }
</style>
</head>
<body>
  <section class="card card--front">
    <div class="brand">
      <div class="brand__name"><span class="brand__square"></span>Nordfeld AG</div>
      <div class="brand__tagline">DIGITALE STRATEGIEN</div>
    </div>

    <ul class="contact">
      <li>
        <svg viewBox="0 0 16 16" aria-hidden="true"><path d="M3.5 1.5l2.5 0 1 3.5-1.8 1.2c.8 1.8 2.2 3.2 4 4l1.2-1.8 3.5 1v2.5c0 .8-.7 1.5-1.5 1.5C6.6 13.4 2.6 9.4 2 3c0-.8.7-1.5 1.5-1.5z"/></svg>
        127 345 9876
      </li>
      <li>
        <svg viewBox="0 0 16 16" aria-hidden="true"><path d="M4 1h8v4H4zM1 6h14v6h-3V9H4v3H1zM5 10h6v5H5z"/></svg>
        345 345 9876
      </li>
      <li>
        <svg viewBox="0 0 16 16" aria-hidden="true"><path d="M1 3h14v1.2L8 9 1 4.2zM1 5.8l7 4.8 7-4.8V13H1z"/></svg>
        info@yourname.com
      </li>
      <li>
        <svg viewBox="0 0 16 16" aria-hidden="true" fill="none"><g stroke="#231f20" stroke-width="1.1" fill="none"><circle cx="8" cy="8" r="6.5"/><ellipse cx="8" cy="8" rx="3" ry="6.5"/><path d="M1.5 8h13M2.5 4.8h11M2.5 11.2h11"/></g></svg>
        www.yourweb.com
      </li>
    </ul>

    <div class="person">
      <div class="person__name">Your name</div>
      <div class="person__title">Job Title</div>
      <address class="person__address">Suite 102 Street name<br>State, Zip 2034,Country</address>
    </div>
  </section>

  <section class="card card--back">
    <div class="back-brand"><span class="back-brand__square"></span>Nordfeld AG</div>
    <div class="back-url">www.yourweb.com</div>
  </section>
</body>
</html>
```